International Clinical Software Company needs a new business card design

We are looking for a new business card design for our company that has recently expanded into the UK market, making us a multinational company.
After having rebranded our website and produced a new style guide, we are looking for a business card that is creative and attention grabbing, while being consistent with the style and colour scheme used on the new website, www.plumvora.example
We produce care management technology for the aged care market, but the main aspect we aim to communicate is the human element of our software, and the way it assists in providing better care for aged people, and stronger relationships between aged people and the staff that care for them.
Our current business card is a dark green with gold text, which makes the text quite difficult to read, not very aesthetically appealing and the colour scheme looks quite dated.
We would like something fresh and modern, that can still be colourful but doesn't use large blocks of dark colour, and uses the colours within our logo.
Something tying in with the leaves that are used in our logo could work quite nicely, along with the Autumn/Fall colours of soft greens, yellows and reds (also in our existing logo). However also happy to look at fresh, completely out of the box ideas we may not have yet considered.
Target Market(s)
The people that receive this business card work in the aged card or health industry and are either corporate/management level staff or clinical (Registered Nurses, care workers etc.)
Industry/Entity Type
Health Product
Contact Information for Business Card
Company Name - BrindlewayCare
Company locations: United Kingdom, Australia, New Zealand
Staff Details:
Staff name: Derek Mallow
Staff job title: Executive Chairman
Staff email: d.mallow@plumvora.example
Office phone number: 01742 918576
Font styles to use
Other font styles liked:
- Calibri
Requirements
Must have
- Must include the BrindlewayCare brand name in it's current font
- Must include logo (3 leaves in gold circle)
- Must include Business Card Details
Nice to have
- Elements of gold
- White space
- Something autumn themed but not too cliched
Should not have
- No blue - used by a major competitor and we would like to differentiate from them
- Large blocks of dark green colour (the green that appears in our leaves on the logo on our current business card is the background colour and it is far too dark)

```html
<!DOCTYPE html>
<html lang="en">
<head>
<meta charset="utf-8">
<title>BrindlewayCare Business Card</title>
<link rel="stylesheet" href="https://fonts.googleapis.com/css2?family=Open+Sans:wght@400;600;700&display=swap">
<style>
  :root {
    --backdrop: #ece8e4;
    --card-crimson: #ab1e3c;
    --card-white: #ffffff;
    --text-light: #ffffff;
    --brand-gold: #d7a21c;
    --brand-tan: #a8936f;
    --leaf-yellow: #f0d22a;
    --leaf-orange: #e98a2a;
    --leaf-red: #c5452a;
    --leaf-brown: #7a3414;
    --leaf-green: #8fa833;
  }
  * { margin: 0; padding: 0; box-sizing: border-box; }
  html, body { width: 1200px; height: 900px; overflow: hidden; }
  body {
    background: var(--backdrop);
    font-family: "Open Sans", Calibri, sans-serif;
    position: relative;
  }
  .card {
    position: absolute;
    overflow: hidden;
    box-shadow: 0 6px 18px rgba(0,0,0,0.18);
  }
  .card-front {
    left: 238px; top: 62px; width: 555px; height: 342px;
    background: var(--card-crimson);
    color: var(--text-light);
  }
  .card-back {
    left: 458px; top: 519px; width: 559px; height: 341px;
    background: var(--card-white);
  }
  .contact { position: absolute; left: 25px; top: 56px; }
  .contact-name { font-size: 17px; font-weight: 700; line-height: 22px; }
  .contact-title { font-size: 15px; line-height: 20px; }
  .contact-email {
    margin-top: 14px; font-size: 14px; line-height: 20px;
    display: flex; align-items: center; gap: 8px;
  }
  .contact-email svg { width: 11px; height: 11px; }
  .contact-locations { margin-top: 14px; font-size: 15px; line-height: 20px; }
  .brand-front {
    position: absolute; right: 28px; top: 66px;
    font-size: 34px; font-weight: 400; letter-spacing: 0.5px;
    color: var(--brand-gold);
  }
  .brand-back {
    position: absolute; left: 32px; top: 112px;
    display: flex; align-items: center; gap: 14px;
  }
  .brand-mark {
    width: 50px; height: 50px; border-radius: 50%;
    border: 2px solid var(--brand-tan);
  }
  .brand-back-name {
    font-size: 38px; font-weight: 400; color: var(--brand-tan);
  }
  .leaf-band { position: absolute; left: 0; bottom: 0; }
</style>
</head>
<body>

  <section class="card card-front">
    <div class="contact">
      <p class="contact-name">Derek Mallow</p>
      <p class="contact-title">Executive Chairman</p>
      <p class="contact-email">
        <svg viewBox="0 0 24 24" aria-hidden="true"><path fill="#fff" d="M6.6 10.8a15 15 0 0 0 6.6 6.6l2.2-2.2c.3-.3.7-.4 1-.2 1.1.4 2.3.6 3.6.6.6 0 1 .4 1 1V20c0 .6-.4 1-1 1A17 17 0 0 1 3 4c0-.6.4-1 1-1h3.5c.6 0 1 .4 1 1 0 1.3.2 2.5.6 3.6.1.3 0 .7-.2 1z"/></svg>
        d.mallow@plumvora.example
      </p>
      <p class="contact-locations">United Kingdom, Australia<br>New Zealand</p>
    </div>
    <p class="brand-front">BrindlewayCare</p>
    <svg class="leaf-band" width="555" height="175" viewBox="0 0 555 175" role="img" aria-label="Illustration of scattered autumn leaves in yellow, orange, red, brown and green">
      <defs>
        <linearGradient id="leavesFront" x1="0" y1="0" x2="1" y2="0">
          <stop offset="0" stop-color="#e07a2a"/>
          <stop offset="0.35" stop-color="#c8652a"/>
          <stop offset="0.6" stop-color="#e99a3a"/>
          <stop offset="0.8" stop-color="#c9502e"/>
          <stop offset="1" stop-color="#f0d22a"/>
        </linearGradient>
      </defs>
      <path fill="url(#leavesFront)" d="M0 150 C60 130 110 95 170 80 C230 70 270 40 330 30 C400 20 450 5 500 0 L555 10 L555 175 L0 175 Z"/>
    </svg>
  </section>

  <section class="card card-back">
    <div class="brand-back">
      <span class="brand-mark"></span>
      <span class="brand-back-name">BrindlewayCare</span>
    </div>
    <svg class="leaf-band" width="559" height="170" viewBox="0 0 559 170" role="img" aria-label="Illustration of scattered autumn leaves in yellow, orange, red, brown and green">
      <defs>
        <linearGradient id="leavesBack" x1="0" y1="0" x2="1" y2="0">
          <stop offset="0" stop-color="#e07a2a"/>
          <stop offset="0.35" stop-color="#c8652a"/>
          <stop offset="0.6" stop-color="#e99a3a"/>
          <stop offset="0.8" stop-color="#c9502e"/>
          <stop offset="1" stop-color="#f0d22a"/>
        </linearGradient>
      </defs>
      <path fill="url(#leavesBack)" d="M0 145 C60 125 110 90 170 78 C230 68 270 38 330 28 C400 18 450 4 500 0 L559 8 L559 170 L0 170 Z"/>
    </svg>
  </section>

</body>
</html>
```